Awsome new website

We are a Fencing Contracting company in Melbourne Australia. We supply and install Timer and Steel boundary fences as well as Pool fencing (e.g. glass, tubular steel). We also manufacture and install swing and sliding gates.

We want a new website that is a modern business website.
We are targeting domestic and business clients.
The design should compliment our logo and company name.
The website needs to be easy to update.

Some specifics we want.
Menu - Main menu at top of page and smaller footer menu (to add different menu items)
Slider - Main page to have a slider on it that's easy for us to add and remove slides.
Call to action - all pages to have a "call to action" logo or icon that attracts attention (see file "call_to_action.pdf)
Instant quote - we have a online quote page we need a distinctive logo or icon to redirect to this page.
Main page to have a product /Service guide (see file "website_idea.jpg")
Main page to have widgets or quick link to
o why choose us
o Brochures
o Gallery

Have a Gallery page formatted with different category galleries. e.g. Timber, Glass, Feature
Maintain the current link to our staff page with password, (link in footer menu)

Hopefully that covers everything.
Our current website is www.tallgumfencing.com.au to have a look at the current site.
regards Doug

• Turn off blogging as we don’t want 100’s of comments from spammers to delete

We would like to implement the Portalio plugin (see "http://portalio-plug.net/" ), but this can be done after the new Theme has been implemented.

```html
<!DOCTYPE html>
<html lang="en">
<head>
<meta charset="utf-8">
<title>Tall Gum Fencing</title>
<link href="https://fonts.googleapis.com/css2?family=Source+Sans+3:wght@400;600&display=swap" rel="stylesheet">
<style>
:root{
  --red:#9b1b1e;
  --red-bright:#c3272b;
  --red-dark:#7e1114;
  --gold:#f6c86a;
  --ink:#333;
  --muted:#777;
  --nav-top:#5a5a5a;
  --nav-bottom:#2e2e2e;
  --panel:#f4f4f4;
  --strip:#efefef;
  --footer:#2b2b2b;
  --footer-text:#bdbdbd;
}
*{margin:0;padding:0;box-sizing:border-box}
html,body{width:1061px;height:1200px;overflow:hidden;background:#fff}
body{position:relative;font-family:"Source Sans 3",sans-serif;color:var(--ink)}
.abs{position:absolute}

.header{position:absolute;left:0;top:0;width:1061px;height:107px;background:#fff}
.brand{position:absolute;left:89px;top:24px;display:flex;align-items:center;gap:8px}
.brand-mark{width:22px;height:22px;background:var(--red)}
.brand-name{font-size:26px;font-weight:600;color:var(--red)}

.nav{position:absolute;left:0;top:107px;width:1061px;height:41px;background:linear-gradient(var(--nav-top),var(--nav-bottom))}
.nav-rule{position:absolute;left:0;top:148px;width:1061px;height:6px;background:var(--red-bright)}
.nav ul{list-style:none;position:absolute;left:89px;top:0;height:41px;display:flex}
.nav li{height:41px;line-height:41px;color:#fff;font-size:14px;font-weight:600;text-transform:uppercase;text-align:center;border-left:1px solid #222;box-shadow:inset 1px 0 0 #666;position:relative}
.nav li:last-child{border-right:1px solid #222}
.nav li.active{background:#262626}
.nav li.active::after{content:"";position:absolute;left:50%;bottom:-1px;margin-left:-6px;border:6px solid transparent;border-bottom-color:var(--red-bright)}

.call-us{position:absolute;left:838px;top:60px}

.slider{position:absolute;left:0;top:154px;width:1061px;height:444px;background:linear-gradient(180deg,#6f8a49 0%,#5f7a3c 40%,#8a8c80 60%,#5d6b3b 100%)}
.slider-caption{position:absolute;left:0;bottom:0;width:100%;height:58px;background:rgba(20,20,20,.78)}
.slider-caption p{position:absolute;left:89px;top:15px;color:#fff;font-size:20px}
.dots{position:absolute;left:896px;top:24px;display:flex;gap:8px}
.dots span{width:13px;height:13px;border-radius:50%;background:#ccc;box-shadow:inset 0 1px 2px #555}
.dots span:first-child{background:#555}

.welcome h1{position:absolute;left:90px;top:622px;font-size:25px;font-weight:600;color:var(--red)}
.intro{position:absolute;left:90px;top:667px;width:594px;font-size:13px;line-height:22px;color:var(--muted);text-align:justify}
.thumb{position:absolute;top:769px;width:192px;height:105px}
.rule{position:absolute;left:93px;top:891px;width:590px;height:1px;background:#ddd}
.services h2{position:absolute;left:92px;top:906px;font-size:20px;font-weight:400;color:var(--red)}
.service{position:absolute;font-size:15px;color:var(--ink);padding-left:18px}
.service::before{content:"";position:absolute;left:0;top:6px;width:5px;height:5px;border-top:1px solid #999;border-right:1px solid #999;transform:rotate(45deg)}
.service::after{content:"";position:absolute;left:11px;top:3px;width:1px;height:14px;background:#ccc}

.cta{position:absolute;left:716px;width:257px;height:64px;border-radius:3px;display:flex;align-items:center;gap:14px;padding-left:28px}
.cta-quote{top:630px;background:linear-gradient(#c8363a,var(--red-dark));border:1px solid #7a1013}
.cta-brochure{top:699px;background:linear-gradient(#4f4f4f,#262626);border:1px solid #1a1a1a}
.cta span{font-size:23px;font-weight:600;color:var(--gold)}

.why h3{position:absolute;left:719px;top:782px;font-size:20px;font-weight:400;color:var(--red)}
.why-box{position:absolute;left:716px;top:819px;width:257px;height:177px;background:var(--panel);border-top:2px solid #e6e6e6;border-bottom:2px solid #e6e6e6;padding:13px 10px 0 12px;font-size:12.5px;line-height:20px;color:var(--muted);text-align:justify}
.why-box p+p{margin-top:8px}
.why-box a{color:#d3272b;text-decoration:none}

.contact-strip{position:absolute;left:0;top:1025px;width:1061px;height:85px;background:var(--strip)}
.contact-item{position:absolute;font-size:12.5px;line-height:21px;color:#888}

.footer{position:absolute;left:0;top:1110px;width:1061px;height:90px;background:var(--footer)}
.footer-menu{position:absolute;left:89px;top:19px;font-size:12.5px;color:var(--footer-text)}
.footer-menu i{font-style:normal;margin:0 9px;color:#888}
.copyright{position:absolute;left:89px;top:51px;font-size:12px;color:var(--footer-text)}
.social{position:absolute;left:858px;top:32px;display:flex;gap:9px}
.social span{width:22px;height:22px;border-radius:50%;background:#6a6a6a;display:flex;align-items:center;justify-content:center}
</style>
</head>
<body>

<header class="header">
  <div class="brand"><span class="brand-mark"></span><span class="brand-name">Tall Gum Fencing</span></div>
</header>

<nav class="nav">
  <ul>
    <li class="active" style="width:84px">Home</li>
    <li style="width:120px">Duracote</li>
    <li style="width:140px">Instant Quote</li>
    <li style="width:97px">Gallery</li>
    <li style="width:178px">Products &amp; Services</li>
    <li style="width:122px">Contact Us</li>
  </ul>
</nav>
<div class="nav-rule"></div>

<svg class="call-us" width="130" height="85" viewBox="0 0 130 85" aria-label="Call us">
  <path d="M18 30 H112 L104 62 Q65 88 26 62 Z" fill="#c3272b" stroke="#fff" stroke-width="3"/>
  <path d="M22 33 H108 L102 58 Q65 80 28 58 Z" fill="url(#cg)"/>
  <defs><linearGradient id="cg" x1="0" y1="0" x2="0" y2="1"><stop offset="0" stop-color="#e0383c"/><stop offset="1" stop-color="#9e1418"/></linearGradient></defs>
  <circle cx="65" cy="25" r="17" fill="#d5292d" stroke="#fff" stroke-width="3"/>
  <path d="M58 20 q2-3 4 0 l1 3 q-1 2 0 3 q2 3 4 4 q1 1 3 0 l3 1 q3 2 0 4 q-4 3-10-2 q-6-6-5-13z" fill="#fff"/>
  <text x="65" y="63" text-anchor="middle" font-family="Source Sans 3, sans-serif" font-weight="600" font-size="17" fill="#f6c86a">CALL US</text>
</svg>

<section class="slider" role="img" aria-label="Photo of a pasture with grazing cattle behind an old steel farm gate">
  <div class="slider-caption">
    <p>Phasellus erat felis, scelerisque a rutrum vitae, malesuada id erat</p>
    <div class="dots"><span></span><span></span><span></span><span></span></div>
  </div>
</section>

<section class="welcome">
  <h1>Welcome to Tall Gum Fencing</h1>
  <p class="intro">Donec tincidunt gravida mauris at mollis. Nulla consectetur magna et purus porttitor, nec sollicitudin felis bibendum. Pellentesque quis malesuada risus. Vivamus vehicula feugiat porttitor. Sed pellentesque ullamcorper volutpat. Praesent volutpat augue ac sapien egestas, feugiat feugiat augue convallis. Aenean neque sapien, mollis eget auctor at, lacinia nec nulla.</p>
  <div class="thumb" style="left:91px;background:linear-gradient(#7a6a52,#5f8a3e 60%,#e8e8e8)" role="img" aria-label="Photo of a white ornamental garden fence on a lawn"></div>
  <div class="thumb" style="left:292px;background:linear-gradient(#6f9a4a,#3d3d33 55%,#4f8a34)" role="img" aria-label="Photo of a black tubular steel gate in a garden"></div>
  <div class="thumb" style="left:492px;background:linear-gradient(#3f6a3a,#7fb0c8 55%,#9a948a)" role="img" aria-label="Photo of a pool with glass and mesh pool fencing"></div>
</section>

<div class="rule"></div>

<section class="services">
  <h2>Tall Gum Fencing Services</h2>
  <div class="service" style="left:93px;top:950px">Tubular Steel Pool Fencing</div>
  <div class="service" style="left:316px;top:950px">Heritage Fencing</div>
  <div class="service" style="left:518px;top:950px">Duracote™ Fencing</div>
  <div class="service" style="left:93px;top:978px">Glass Pool Fencing</div>
  <div class="service" style="left:316px;top:978px">Timber Paling Fencing</div>
</section>

<a class="cta cta-quote">
  <svg width="40" height="42" viewBox="0 0 40 42" aria-hidden="true"><path d="M6 4 H28 L34 10 V38 H6 Z" fill="#f5f5f5" stroke="#999"/><path d="M11 14 H29 M11 19 H29 M11 24 H29 M11 29 H22" stroke="#999" stroke-width="1.5"/><path d="M24 34 L36 16 L39 18 L27 36 Z" fill="#e3a93a"/></svg>
  <span>Get QuickQuote</span>
</a>
<a class="cta cta-brochure">
  <svg width="40" height="42" viewBox="0 0 40 42" aria-hidden="true"><path d="M6 3 H28 L34 9 V39 H6 Z" fill="#f5f5f5" stroke="#999"/><rect x="10" y="11" width="18" height="20" rx="2" fill="#d5292d"/></svg>
  <span>Get Our Broucher</span>
</a>

<section class="why">
  <h3>Why Choose us?</h3>
  <div class="why-box">
    <p>Nunc bibendum nunc eget nisl molestie, eu dictum dui imperdiet. Nam a augue ac ligula pulvinar rhoncus.</p>
    <p>Nunc vitae congue lorem. Nunc ut diam sed velit sollicitudin ullamcorper in a libero. Duis iaculis vulputate nisl, vel tristique sapien scelerisque eget. <a>More</a></p>
  </div>
</section>

<section class="contact-strip">
  <svg class="abs" style="left:134px;top:30px" width="22" height="26" viewBox="0 0 22 26" aria-hidden="true"><rect x="1" y="2" width="20" height="23" fill="#aaa"/><rect x="5" y="6" width="4" height="15" fill="#fff"/><rect x="13" y="6" width="4" height="15" fill="#fff"/></svg>
  <div class="contact-item" style="left:167px;top:21px">55, Building name, Street name<br>City - Zipcode</div>
  <svg class="abs" style="left:422px;top:30px" width="26" height="26" viewBox="0 0 26 26" aria-hidden="true"><path d="M3 5 q3-5 7-1 l-2 4 q3 6 8 9 l4-2 q4 4-1 7 q-8 2-14-7 q-4-6-2-10z" fill="#aaa"/></svg>
  <div class="contact-item" style="left:459px;top:21px">Phone &nbsp;&nbsp;: 503.555.0142<br>Toll Free: 888.555.0199</div>
  <svg class="abs" style="left:697px;top:35px" width="24" height="17" viewBox="0 0 24 17" aria-hidden="true"><rect width="24" height="17" fill="#aaa"/><path d="M1 1 L12 10 L23 1" stroke="#fff" stroke-width="1.5" fill="none"/></svg>
  <div class="contact-item" style="left:732px;top:32px">E-mail : info@tallgumfencing.com.au</div>
</section>

<footer class="footer">
  <div class="footer-menu">Home<i>|</i>Duracote<i>|</i>Instant Quote<i>|</i>Gallery<i>|</i>Products &amp; Services<i>|</i>Contact us</div>
  <div class="copyright">Copyright &nbsp;© &nbsp;2013 &nbsp;&nbsp;&nbsp;Tall Gum Fencing. &nbsp;&nbsp;All rights reserved.</div>
  <div class="social">
    <span aria-label="Social link"></span>
    <span aria-label="Social link"></span>
    <span aria-label="Social link"></span>
    <span aria-label="Email"><svg width="12" height="9" viewBox="0 0 12 9"><rect x=".5" y=".5" width="11" height="8" fill="none" stroke="#2b2b2b"/><path d="M.5 .5 L6 5 L11.5 .5" fill="none" stroke="#2b2b2b"/></svg></span>
  </div>
</footer>

</body>
</html>
```